Luxury Wine Label for New Startup Winery

We need a wine label for our new winery startup. We have worked with a local designer but do not feel the resulting label / logo have the elevation required to present our brand as a luxury wine. Our winery is called "Quailbrook Vineyards" and we are focused on extremely high quality hand crafted artisan and estate wines from the Pacific Northwest.
We would like to see designs that utilize a tree line, or other imagery that represents the "Quailbrook" part of our company name. Another interesting feature could be wood grain.
A logo will be required based on your design so please design with this in mind:
This logo should be consistent with the wine bottle label design, and should be representative of our high end exclusive wine while giving a sense of place (Oregon/ Pacific Northwest.)
I will supply an image of the design we received from our local designer, PLEASE NOTE: in general we do like wood grain and tree line concepts but feel the execution was poorly done.
ATTN: Logo design should be suitable for use on: Bottles (Red wine/rose/white wine), Bussiness cards, vehicle signage, business signage, etc
P.S.:
If you have a design that is not outside the box we are still interested in seeing it.
Label is for a burgundy style bottle with a label height of 3.5 - 4" and a width of 3.5-4"
any label <= 4"x4" and >=3.5"x3.5" will be acceptable:
HOWEVER Width should be greater than or equal to height due to the bottle format
Target Market(s)
Wine enthusiasts with adequate discretionary budgets to afford $100 bottles of wine.
Industry/Entity Type
Wine / Winery
Requirements
Must have
- A sense of luxury, a feel of exclusivity, and a theme consistent with our product and brand name
Nice to have
- Tree line, wood grain or other wood themes. Serif fonts
Should not have
- anything cheesy, off topic, hard to read script fonts or anything that makes the label hard to read from a few feet away or too busy

```html
<!DOCTYPE html>
<html lang="en">
<head>
<meta charset="utf-8">
<title>Quailbrook Vineyards – Wine Labels</title>
<link rel="stylesheet" href="https://fonts.googleapis.com/css2?family=Cinzel:wght@400;500&display=swap">
<style>
  :root {
    --page-bg: #ffffff;
    --ink: #1d1a1a;
    --rose-ink: #b5587c;
    --rose-frame: #2a2626;
    --syrah-frame: #c3884c;
    --rose-grain-light: #fefafc;
    --rose-grain-mid: #f8e3eb;
    --rose-grain-deep: #f3d2de;
    --syrah-grain-light: #fffcf8;
    --syrah-grain-mid: #f9ebdb;
    --syrah-grain-deep: #f3dcc2;
    --forest-top: #8a8686;
    --forest-bottom: #3a3737;
  }
  * { margin: 0; padding: 0; box-sizing: border-box; }
  html, body {
    width: 1200px; height: 1200px; overflow: hidden;
    background: var(--page-bg);
  }
  .label-sheet {
    position: relative; width: 1200px; height: 1200px;
  }
  .label {
    position: absolute; top: 340px; width: 520px; height: 520px;
    font-family: "Cinzel", "Times New Roman", serif;
    color: var(--ink);
    text-align: center;
    overflow: hidden;
  }
  .label--rose {
    left: 50px;
    border: 1.5px solid var(--rose-frame);
  }
  .label--syrah {
    left: 630px;
    border: 1.5px solid var(--syrah-frame);
  }
  .wood-grain {
    position: absolute; inset: 0;
  }
  .label--rose .wood-grain {
    background:
      radial-gradient(ellipse 42% 52% at 26% 45%, var(--rose-grain-deep), transparent 75%),
      linear-gradient(100deg, var(--rose-grain-mid), var(--rose-grain-light) 55%, var(--rose-grain-mid));
  }
  .label--syrah .wood-grain {
    background:
      radial-gradient(ellipse 38% 50% at 76% 52%, var(--syrah-grain-deep), transparent 75%),
      linear-gradient(100deg, var(--syrah-grain-mid), var(--syrah-grain-light) 55%, var(--syrah-grain-mid));
  }
  .brand-mark {
    position: absolute; left: 50%; top: 23px;
    width: 50px; height: 50px; margin-left: -25px;
    border: 2px solid var(--ink); border-radius: 50%;
  }
  .brand-name {
    position: absolute; left: 0; right: 0; top: 92px;
    font-size: 29px; font-weight: 500; letter-spacing: 0.5px; line-height: 1;
  }
  .brand-sub {
    position: absolute; left: 0; right: 0; top: 125px;
    font-size: 15px; letter-spacing: 4px; line-height: 1;
  }
  .varietal {
    position: absolute; left: 0; right: 0; line-height: 1;
  }
  .label--rose .varietal {
    top: 170px; font-size: 64px; letter-spacing: 12px;
    color: var(--rose-ink); padding-left: 12px;
  }
  .label--syrah .varietal {
    top: 178px; font-size: 42px; letter-spacing: 14px; padding-left: 14px;
  }
  .varietal-rule {
    position: absolute; left: 186px; top: 234px;
    width: 150px; height: 1.5px; background: var(--ink);
  }
  .forest-art {
    position: absolute;
    background: linear-gradient(180deg, var(--forest-top), var(--forest-bottom));
    opacity: 0.8;
  }
  .label--rose .forest-art {
    left: 148px; top: 262px; width: 226px; height: 176px;
  }
  .label--syrah .forest-art {
    left: 184px; top: 240px; width: 152px; height: 172px;
  }
  .region {
    position: absolute; left: 0; right: 0; top: 438px;
    font-size: 16px; letter-spacing: 4px; line-height: 1; padding-left: 4px;
  }
  .vintage {
    position: absolute; left: 0; right: 0; top: 474px;
    font-size: 24px; letter-spacing: 5px; line-height: 1; padding-left: 5px;
  }
</style>
</head>
<body>
<main class="label-sheet">
  <section class="label label--rose">
    <div class="wood-grain" role="img" aria-label="Soft pink wood grain pattern with a knot on the left, covering the whole label"></div>
    <div class="brand-mark"></div>
    <div class="brand-name">QUAILBROOK</div>
    <div class="brand-sub">VINEYARDS</div>
    <div class="varietal">ROSE</div>
    <div class="forest-art" role="img" aria-label="Black ink illustration of a dense stand of evergreen trees"></div>
  </section>

  <section class="label label--syrah">
    <div class="wood-grain" role="img" aria-label="Soft tan wood grain pattern with a knot on the right, covering the whole label"></div>
    <div class="brand-mark"></div>
    <div class="brand-name">QUAILBROOK</div>
    <div class="brand-sub">VINEYARDS</div>
    <div class="varietal">SYRAH</div>
    <div class="varietal-rule"></div>
    <div class="forest-art" role="img" aria-label="Black ink illustration of a tall cluster of evergreen trees"></div>
    <div class="region">WILLAMETTE VALLEY</div>
    <div class="vintage">2024</div>
  </section>
</main>
</body>
</html>
```